Veterinary Pylon

My veterinary clinic is not clearly visible from the street and I want to place a Pylon next to my driveway. I want a modern, elegant straight Design, the Photo shows the sheduled place. One can see the clinic on our Homepage: www.tailbright-vethaus.at
The last pictures are examples for pylones I like

Target Market(s)

the passing cars often miss my entry...I want to show where to turn left

Colors
3276b5
33a6d7
00a990

Requirements
Must have
• High value, simple elegance, size: 250cm (high) x 100cm (width)
Nice to have
• Our Logo, arrow(?)

A special Text is not necessary but this will be an option:

Biegen sie hier ab und wir biegen es wieder hin!
Should not have
• Too much Color, the colors I have chosen are the possible colors but it‘s not necessary to use them.

```html
<!DOCTYPE html>
<html lang="de">
<head>
<meta charset="utf-8">
<title>Tailbright Vethaus – Pylon</title>
<link rel="stylesheet" href="https://fonts.googleapis.com/css2?family=Archivo+Black&display=swap">
<style>
  :root {
    --navy: #114b93;
    --sky: #2dbbdd;
    --teal: #03aa8e;
    --white: #ffffff;
  }
  html, body {
    margin: 0;
    padding: 0;
    width: 1200px;
    height: 3000px;
    overflow: hidden;
    background: var(--white);
  }
  .pylon {
    position: relative;
    width: 1200px;
    height: 3000px;
    overflow: hidden;
    background: var(--white);
  }
  .pylon__art {
    position: absolute;
    inset: 0;
    width: 1200px;
    height: 3000px;
  }
  .brand {
    position: absolute;
    left: 0;
    right: 0;
    top: 110px;
    display: flex;
    flex-direction: column;
    align-items: center;
  }
  .brand__dot {
    width: 300px;
    height: 300px;
    border-radius: 50%;
    background: var(--sky);
    margin-bottom: 150px;
  }
  .brand__name {
    margin: 0;
    font-family: "Archivo Black", "Arial Black", sans-serif;
    font-weight: 400;
    color: var(--navy);
    text-align: center;
    text-transform: uppercase;
    line-height: 1.02;
    font-size: 118px;
    letter-spacing: 2px;
  }
</style>
</head>
<body>
<main class="pylon">
  <svg class="pylon__art" viewBox="0 0 1200 3000" xmlns="http://www.w3.org/2000/svg" aria-hidden="true">
    <!-- lower colour waves -->
    <path class="wave wave--teal" fill="var(--teal)"
          d="M0 1791 C250 1800 450 1860 640 1960 L640 3000 L0 3000 Z"/>
    <path class="wave wave--gap" fill="var(--white)"
          d="M0 2222 C300 1868 700 1758 955 1756 C1040 1756 1120 1766 1200 1782 L1200 3000 L0 3000 Z"/>
    <path class="wave wave--sky" fill="var(--sky)"
          d="M0 2254 C300 1900 700 1790 955 1788 C1040 1788 1120 1798 1200 1814 L1200 3000 L0 3000 Z"/>

    <!-- turn-left arrow button -->
    <g class="turn-sign">
      <circle cx="592" cy="1785" r="269" fill="var(--navy)" fill-opacity="0.3"/>
      <circle cx="592" cy="1785" r="226" fill="var(--navy)"/>
      <circle cx="592" cy="1785" r="197" fill="none" stroke="var(--white)" stroke-width="12"/>
      <path d="M475 1785 H724" stroke="var(--white)" stroke-width="20" fill="none"/>
      <path d="M564 1682 L461 1785 L564 1888" stroke="var(--white)" stroke-width="20" fill="none" stroke-linejoin="miter"/>
    </g>
  </svg>

  <header class="brand">
    <div class="brand__dot"></div>
    <h1 class="brand__name">Tailbright<br>Vethaus</h1>
  </header>
</main>
</body>
</html>
```